Ward Compass Business Card Design*

We need a business card design for our company Ward Compass. Our company is specialized in providing online consulting services regarding medical institutions, hospitals and doctors. We work with patients worldwide looking to choose between healthcare providers. We have a website you may use as a reference, where we list doctors and clinics worldwide. So we target Medical providers as well as patients worldwide.
Target Market(s)
Medical Providers and patients around the world
Industry/Entity Type
Medical
Contact Information for Business Card
Salwa Kettani
CEO
+90 612 348 2175
info@wardcompass.example
www.wardcompass.example
14 Annakhil 7 H.R.B. Rabat, Morocco
Requirements
Must have
- Company logo/name on one full side, personal info and smaller logo and company name on the other side.
Nice to have
- Smart and elegant design

```html
<!DOCTYPE html>
<html lang="en">
<head>
<meta charset="utf-8">
<title>Ward Compass Business Card</title>
<link rel="stylesheet" href="https://fonts.googleapis.com/css2?family=Lato:wght@400;700;900&display=swap">
<style>
  :root {
    --navy: #163766;
    --grey: #828488;
    --white: #ffffff;
    --ink: #1c1c1c;
    --stage: #e9eaec;
  }
  * { box-sizing: border-box; margin: 0; padding: 0; }
  html, body { width: 1200px; height: 900px; overflow: hidden; }
  body {
    background: var(--stage);
    font-family: "Lato", sans-serif;
    position: relative;
  }
  .card {
    position: absolute;
    width: 700px;
    height: 360px;
    left: 250px;
    overflow: hidden;
    box-shadow: 0 6px 18px rgba(0,0,0,0.18);
  }
  /* Back side */
  .card-back { top: 60px; background: var(--navy); }
  .card-back .brand {
    position: absolute;
    top: 120px; left: 0; right: 0;
    display: flex; align-items: center; justify-content: center; gap: 18px;
  }
  .brand-dot {
    width: 56px; height: 56px; border-radius: 50%;
    background: var(--grey);
  }
  .card-back .brand-name {
    font-size: 52px; font-weight: 700; color: var(--white);
    letter-spacing: 1px;
  }
  .card-back .web {
    position: absolute; top: 250px; left: 0; right: 0;
    text-align: center; color: var(--white);
    font-size: 20px; letter-spacing: 1px;
  }
  /* Front side */
  .card-front { top: 480px; background: var(--white); }
  .card-front .band { position: absolute; inset: 0; }
  .card-front .brand {
    position: absolute; top: 34px; left: 48px;
    display: flex; align-items: center; gap: 14px;
  }
  .card-front .brand-dot { width: 42px; height: 42px; background: var(--navy); }
  .card-front .brand-name {
    font-size: 38px; font-weight: 700; color: var(--navy);
    letter-spacing: 1px;
  }
  .contact {
    position: absolute; top: 120px; left: 48px;
    font-size: 17px; color: var(--ink); line-height: 1.4;
  }
  .contact .address { margin-bottom: 10px; }
  .contact-line { display: flex; align-items: center; gap: 10px; }
  .contact-line svg { width: 14px; height: 14px; fill: var(--navy); }
  .person {
    position: absolute; top: 180px; left: 440px;
  }
  .person .name { font-size: 30px; font-weight: 700; color: var(--navy); }
  .person .role { font-size: 20px; color: var(--ink); }
  .card-front .web {
    position: absolute; right: 50px; bottom: 16px;
    color: var(--white); font-size: 22px; letter-spacing: 0.5px;
  }
</style>
</head>
<body>

  <section class="card card-back">
    <div class="brand">
      <span class="brand-dot"></span>
      <span class="brand-name">WARD COMPASS</span>
    </div>
    <p class="web">www.wardcompass.example</p>
  </section>

  <section class="card card-front">
    <svg class="band" viewBox="0 0 700 360" preserveAspectRatio="none">
      <path d="M0,248 Q380,330 700,262 L700,282 Q360,340 0,252 Z" fill="var(--grey)"/>
      <path d="M0,258 Q360,348 700,292 L700,360 L0,360 Z" fill="var(--navy)"/>
    </svg>

    <div class="brand">
      <span class="brand-dot"></span>
      <span class="brand-name">WARD COMPASS</span>
    </div>

    <div class="contact">
      <p class="address">14 Annakhil 7<br>H.R.B. Rabat, Morocco</p>
      <p class="contact-line">
        <svg viewBox="0 0 24 24"><path d="M6.6 10.8a15.1 15.1 0 0 0 6.6 6.6l2.2-2.2a1 1 0 0 1 1-.25 11.4 11.4 0 0 0 3.6.57 1 1 0 0 1 1 1V20a1 1 0 0 1-1 1A17 17 0 0 1 3 4a1 1 0 0 1 1-1h3.5a1 1 0 0 1 1 1c0 1.25.2 2.45.57 3.57a1 1 0 0 1-.25 1z"/></svg>
        +90 612 348 2175
      </p>
      <p class="contact-line">
        <svg viewBox="0 0 24 24"><path d="M2 5h20v14H2z M2 5l10 8 10-8" fill="var(--navy)" stroke="var(--white)" stroke-width="1.5"/></svg>
        info@wardcompass.example
      </p>
    </div>

    <div class="person">
      <p class="name">Salwa Kettani</p>
      <p class="role">CEO</p>
    </div>

    <p class="web">www.wardcompass.example</p>
  </section>

</body>
</html>
```